Local massage therapist needs some new marketing material

Hi there! I am a massage therapist here in Denver, CO in Alder Bend(shopping and art district) of the city. My business is called Lumo Bodywork of Denver. My practice has an eastern influence and I do reflexology, thai massage and use Chinese herbs, etc. I know all my clients and pay close attention to details. I am also very respectful of tradition and it shows in how I work. I tend to like modern, clean, fun, Asian designs. I am wanting a new business card and brochure. I have a logo and branding for my business that I want used in the design. Currently, the sign for my building is purple and I think my logo was designed to be purple. I will attach pictures of it and can send whatever files are necessary so it can be integrated into the brochure, etc. I like the purple but open to using other colors as well. Thanks!
My website is lumobodyworkofdenver.example where info can be gathered about me and services/fees for brochure.
Updates

Just increased budget. Please see new feedback in discussion thread.

Thanks!

                                       HEY ALL,

Just wanted to let you know that I made a change to my website. It is on the Prices Page. I no longer have the frequent  flyer prices but I added discounts. Let me know if you have any questions. Thanks so much!

Target Market(s)

healthy, urban, educated, upper middle class, yogis

Industry/Entity Type

Marketing

Requirements
Must have
• logo stays purple
Should not have
• not too busy

```html
<!DOCTYPE html>
<html lang="en">
<head>
<meta charset="utf-8">
<title>Lumo Bodywork of Denver – Business Card</title>
<link href="https://fonts.googleapis.com/css2?family=Raleway:wght@200;400;600&family=PT+Serif:wght@400;700&display=swap" rel="stylesheet">
<style>
  :root {
    --bg: #ecebee;
    --purple: #6d1f9c;
    --purple-deep: #5a1683;
    --purple-mid: #8a3fb8;
    --lavender: #c9b2dc;
    --grey: #d9d8dc;
    --white: #ffffff;
    --ink: #4a2a5e;
  }
  * { box-sizing: border-box; margin: 0; padding: 0; }
  html, body { width: 1200px; height: 872px; overflow: hidden; }
  body {
    background: var(--bg);
    position: relative;
    font-family: "PT Serif", Georgia, serif;
  }
  .card {
    position: absolute;
    top: 281px;
    width: 540px;
    height: 309px;
    background: var(--purple);
    overflow: hidden;
    box-shadow: 0 6px 18px rgba(40, 10, 60, .18);
  }
  .card--back { left: 40px; }
  .card--front { left: 620px; }

  /* back side */
  .ornament {
    position: absolute;
    background: radial-gradient(ellipse at center, rgba(201,178,220,.45), rgba(201,178,220,0) 70%);
  }
  .card--back .ornament { left: 10px; top: 8px; width: 200px; height: 90px; }
  .contact-band {
    position: absolute;
    left: 0; right: 0; top: 104px; height: 92px;
    display: flex;
  }
  .contact-cell {
    flex: 1;
    background: var(--grey);
    display: flex;
    align-items: center;
    gap: 10px;
    padding: 0 14px;
    color: var(--ink);
    font-size: 11px;
    line-height: 1.35;
  }
  .contact-cell--phone { background: var(--purple-mid); color: var(--white); }
  .contact-cell svg { flex: none; width: 22px; height: 22px; }
  .visit-note {
    position: absolute;
    left: 0; right: 0; top: 218px;
    text-align: center;
    color: var(--white);
    font-size: 15px;
    line-height: 1.6;
  }
  .visit-note .hours { font-size: 13px; }

  /* front side */
  .corner-squares {
    position: absolute; left: 0; top: 0;
    display: flex; gap: 6px;
  }
  .corner-squares span { width: 26px; height: 16px; background: var(--lavender); }
  .corner-squares span:first-child { background: var(--white); }
  .brand {
    position: absolute; left: 40px; top: 70px;
    display: flex; align-items: center; gap: 14px;
  }
  .brand-mark {
    width: 46px; height: 46px; border-radius: 50%;
    border: 1.5px solid var(--white);
  }
  .brand-name {
    font-family: "Raleway", Arial, sans-serif;
    font-weight: 200;
    color: var(--white);
    font-size: 26px;
    letter-spacing: 2px;
    text-transform: uppercase;
    line-height: 1.15;
  }
  .website {
    position: absolute; left: 40px; top: 150px;
    font-family: "Raleway", Arial, sans-serif;
    font-size: 11px; color: var(--white); letter-spacing: .5px;
  }
  .stripe { position: absolute; left: 0; height: 20px; }
  .stripe--white { top: 208px; width: 360px; background: var(--grey); }
  .stripe--lavender { top: 240px; width: 300px; background: var(--lavender); }
  .card--front .ornament { right: 0; bottom: 0; width: 170px; height: 140px; }
</style>
</head>
<body>

<section class="card card--back" aria-label="Card back">
  <div class="ornament" role="img" aria-label="Soft lavender floral swirl decoration"></div>

  <div class="contact-band">
    <div class="contact-cell contact-cell--address">
      <svg viewBox="0 0 24 24" aria-hidden="true"><path d="M12 3 2 12h3v8h5v-5h4v5h5v-8h3z" fill="#6d1f9c"/></svg>
      <p>2140 E Alder Ave<br>Denver, CO 80206<br>P. 303-555-0142</p>
    </div>
    <div class="contact-cell contact-cell--phone">
      <svg viewBox="0 0 24 24" aria-hidden="true"><path d="M6.6 10.8a15 15 0 0 0 6.6 6.6l2.2-2.2a1 1 0 0 1 1-.25 11.4 11.4 0 0 0 3.6.6 1 1 0 0 1 1 1V20a1 1 0 0 1-1 1A17 17 0 0 1 3 4a1 1 0 0 1 1-1h3.5a1 1 0 0 1 1 1c0 1.25.2 2.45.6 3.6a1 1 0 0 1-.25 1z" fill="#ffffff"/></svg>
      <p>+1 303-555-0142<br>+1 303-555-0187</p>
    </div>
    <div class="contact-cell contact-cell--email">
      <svg viewBox="0 0 24 24" aria-hidden="true"><rect x="2" y="5" width="20" height="14" fill="#6d1f9c"/><path d="M2 5l10 8 10-8" fill="none" stroke="#d9d8dc" stroke-width="1.5"/></svg>
      <p>info@lumobodyworkofdenver<br>.example</p>
    </div>
  </div>

  <div class="visit-note">
    <p>(Appointments required) No walk-ins please</p>
    <p class="hours">Tues – Fri 10am – 8pm &nbsp; Sat 10am – 5pm</p>
  </div>
</section>

<section class="card card--front" aria-label="Card front">
  <div class="corner-squares"><span></span><span></span></div>
  <div class="brand">
    <span class="brand-mark"></span>
    <p class="brand-name">Lumo Bodywork<br>of Denver</p>
  </div>
  <p class="website">www.lumobodyworkofdenver.example</p>
  <div class="stripe stripe--white"></div>
  <div class="stripe stripe--lavender"></div>
  <div class="ornament" role="img" aria-label="Soft lavender flower and swirl decoration"></div>
</section>

</body>
</html>
```